Talvoro bonds (Surety bond broker)

We are a broker of surety bonds, we need a presentation and a flyer with fresh design. Our core values are reliable, on time and customized service. We want to transmit to our clients, they can leave on us the process of underwriting and issuing a surety bond, so they can focus on their business with no distractions.

Font styles to use
Sans Serif
Other font styles liked:

Requirements
Must have
• Visually attractive.
Main Message: Fast service issuing and underwriting surety bonds, reliable, nos surprises, we are always one step ahead, customized and personalized bonding solutions.
Nice to have
• Have short version for the flyer, and extended version for the presentation.
Should not have
• We already have a logo (attached), maintain colors

```html
<!DOCTYPE html>
<html lang="es">
<head>
<meta charset="utf-8">
<title>Talvoro – Presentación</title>
<link href="https://fonts.googleapis.com/css2?family=Montserrat:wght@400;500;600;700&display=swap" rel="stylesheet">
<style>
  :root{
    --page:#ffffff;
    --slate:#4c4c4e;
    --slate-dark:#3e4144;
    --green:#7ac143;
    --green-soft:rgba(122,193,67,.75);
    --white:#ffffff;
    --ink:#222222;
  }
  *{box-sizing:border-box;margin:0;padding:0}
  html,body{width:1200px;height:3178px;overflow:hidden;background:var(--page)}
  body{position:relative;font-family:'Montserrat',sans-serif;color:var(--white)}
  .slide{position:absolute;left:105px;width:990px;height:556px;background:var(--slate);overflow:hidden}
  .slide--cover{top:115px}
  .slide--index{top:715px;background:linear-gradient(180deg,#3f4245 0%,#55585b 55%,#5d6063 100%)}
  .slide--about{top:1315px}
  .slide--offer{top:1915px}
  .slide--services{top:2514px}
  .art{position:absolute;inset:0;width:990px;height:556px}
  .wordmark{position:absolute;font-weight:500;color:var(--green);letter-spacing:.02em}
  .cover-logo{left:66px;top:64px;font-size:54px}
  .cover-title{position:absolute;left:66px;top:278px;font-weight:700;font-size:41px;line-height:1.3}
  .cover-title .accent{color:var(--green);display:block}
  .dash{display:block;width:38px;height:5px;background:var(--green);margin-top:16px}
  .cover-web{position:absolute;left:66px;top:478px;font-size:19px;font-weight:600;letter-spacing:.32em}
  .cover-web .hl,.footer-web .hl{color:var(--green)}
  .globe{display:inline-block;width:14px;height:14px;border:1.5px solid var(--green);border-radius:50%;margin-right:8px;vertical-align:middle}
  .footer-web{position:absolute;left:82px;top:514px;font-size:11px;font-weight:600;letter-spacing:.22em}
  .footer-web .globe{width:10px;height:10px;margin-right:5px;border-width:1px}
  .footer-logo{left:790px;top:511px;font-size:21px}
  .page-no{position:absolute;left:914px;top:513px;width:20px;height:20px;border-radius:50%;background:var(--white);color:var(--ink);font-size:11px;font-weight:700;text-align:center;line-height:20px}
  .index{position:absolute;left:228px;top:56px;color:var(--ink)}
  .index h2{font-size:30px;font-weight:600;color:var(--green)}
  .index .dash{width:12px;height:3px;margin-top:6px}
  .index ol{list-style:none;margin-top:18px}
  .index li{font-size:14px;font-weight:500;height:33px;line-height:20px;position:relative}
  .index li span{position:absolute;left:-33px;top:0;width:20px;height:20px;border-radius:50%;background:var(--green);color:var(--white);font-size:10px;font-weight:700;text-align:center;line-height:20px}
  .copy{position:absolute;left:84px;top:56px;width:414px}
  .copy h2{font-size:30px;font-weight:600;line-height:1.2}
  .copy h2 .accent{color:var(--green)}
  .copy .dash{width:20px;height:3px;margin-top:14px;margin-bottom:30px}
  .copy p{font-size:12.2px;line-height:1.42;margin-bottom:23px}
  .offer p{text-align:justify;margin-bottom:15px}
  .lead{color:var(--green);font-weight:600;display:block}
  .offer .lead-gap{margin-top:28px}
  .hl-green{color:var(--green)}
  .services{list-style:none}
  .services li{position:relative;padding-left:22px;font-size:13.4px;font-weight:500;line-height:1.28;margin-bottom:18px}
  .services li::before{content:"";position:absolute;left:2px;top:2px;width:5px;height:10px;border-right:2px solid var(--green);border-bottom:2px solid var(--green);transform:rotate(40deg)}
  .services small{display:block;font-size:8px;font-weight:400;opacity:.8;margin-top:3px}
</style>
</head>
<body>

<!-- Cover -->
<section class="slide slide--cover">
  <svg class="art" viewBox="0 0 990 556">
    <defs><linearGradient id="coverPhoto" x1="0" y1="0" x2="1" y2="1">
      <stop offset="0" stop-color="#5d7aa8"/><stop offset=".45" stop-color="#c9b07a"/><stop offset=".75" stop-color="#e9e6e2"/><stop offset="1" stop-color="#e8893f"/></linearGradient></defs>
    <circle cx="683" cy="253" r="258" fill="url(#coverPhoto)" role="img" aria-label="Fotomontaje de obra: casco amarillo, planos enrollados y ciudad en construcción"/>
    <path d="M 520 45 A 275 275 0 0 0 690 535" fill="none" stroke="var(--green)" stroke-width="2"/>
    <path d="M 830 15 A 275 275 0 0 1 958 260" fill="none" stroke="var(--green)" stroke-width="2"/>
  </svg>
  <div class="wordmark cover-logo">Talvoro</div>
  <h1 class="cover-title">Tu éxito<span class="accent">Nuestra Pasión</span><span class="dash"></span></h1>
  <div class="cover-web"><span class="globe"></span>www.<span class="hl">talvoro</span>.com</div>
</section>

<!-- Index -->
<section class="slide slide--index">
  <svg class="art" viewBox="0 0 990 556">
    <rect x="440" y="0" width="550" height="556" fill="#54575a" opacity=".35" role="img" aria-label="Fondo tenue de grúas y edificios en construcción"/>
    <circle cx="329" cy="223" r="257" fill="var(--white)"/>
    <path d="M 190 10 A 272 272 0 0 0 330 488" fill="none" stroke="var(--green)" stroke-width="1.5"/>
    <path d="M 460 0 A 272 272 0 0 1 590 260" fill="none" stroke="var(--slate-dark)" stroke-width="1.5"/>
    <path d="M 240 523 H 750 L 776 491 H 934" fill="none" stroke="var(--green)" stroke-width="1"/>
  </svg>
  <div class="index">
    <h2>Índice</h2><span class="dash"></span>
    <ol>
      <li><span>1</span>¿Quiénes somos?</li>
      <li><span>2</span>Oferta de Valor</li>
      <li><span>3</span>Nuestros Servicios</li>
      <li><span>4</span>Productos</li>
      <li><span>5</span>Ciclo de administración de Fianzas</li>
      <li><span>5</span>Nuestros socios de negocio</li>
      <li><span>7</span>Contacto</li>
    </ol>
  </div>
  <div class="footer-web"><span class="globe"></span>www.<span class="hl">talvoro</span>.com</div>
  <div class="wordmark footer-logo">Talvoro</div>
  <div class="page-no">1</div>
</section>

<!-- About -->
<section class="slide slide--about">
  <svg class="art" viewBox="0 0 990 556">
    <defs><linearGradient id="aboutPhoto" x1="0" y1="0" x2="0" y2="1">
      <stop offset="0" stop-color="#3f86c4"/><stop offset=".45" stop-color="#a9c3d6"/><stop offset=".7" stop-color="#c9a25a"/><stop offset="1" stop-color="#4a3c2e"/></linearGradient></defs>
    <circle cx="773" cy="222" r="222" fill="url(#aboutPhoto)" role="img" aria-label="Grúa amarilla sobre edificio en construcción con obreros"/>
    <path d="M 660 -10 A 234 234 0 0 0 700 446" fill="none" stroke="var(--green)" stroke-width="1.5"/>
    <circle cx="608" cy="366" r="40" fill="var(--green-soft)"/>
    <circle cx="657" cy="412" r="24" fill="var(--green-soft)"/>
    <path d="M 240 523 H 750 L 776 491 H 934" fill="none" stroke="var(--green)" stroke-width="1"/>
  </svg>
  <div class="copy">
    <h2>¿Quiénes <span class="accent">somos?</span></h2><span class="dash"></span>
    <p>Talvoro Bonds, somos un grupo de jóvenes emprendedores, con amplia experiencia en el sector afianzador.</p>
    <p>Estamos convencidos de que nuestro principal diferenciador es la pasión por el servicio.</p>
    <p>Nuestra prioridad es el éxito de cada uno de nuestros clientes, nos aseguramos de que el “trámite” de fianzas deje de ser un “trámite” y se convierta en la llave del éxito para cada uno de nuestros fiados y beneficiarios.</p>
    <p>Buscamos siempre tener relaciones estrechas y de largo plazo con todos nuestros “stakeholders”. Por lo que nos rodeamos del mejor talento en el sector para garantizar a nuestros clientes un servicio personalizado, en tiempo y confiable.</p>
  </div>
  <div class="footer-web"><span class="globe"></span>www.<span class="hl">talvoro</span>.com</div>
  <div class="wordmark footer-logo">Talvoro</div>
  <div class="page-no">2</div>
</section>

<!-- Offer -->
<section class="slide slide--offer">
  <svg class="art" viewBox="0 0 990 556">
    <defs><linearGradient id="offerPhoto" x1="0" y1="0" x2="0" y2="1">
      <stop offset="0" stop-color="#7fa6c4"/><stop offset=".5" stop-color="#e9c79a"/><stop offset=".75" stop-color="#d88b3c"/><stop offset="1" stop-color="#2c2a2a"/></linearGradient></defs>
    <circle cx="773" cy="222" r="222" fill="url(#offerPhoto)" role="img" aria-label="Siluetas de obreros en andamios al atardecer con cubeta de concreto"/>
    <path d="M 660 -10 A 234 234 0 0 0 700 446" fill="none" stroke="var(--green)" stroke-width="1.5"/>
    <circle cx="608" cy="366" r="40" fill="var(--green-soft)"/>
    <circle cx="657" cy="412" r="24" fill="var(--green-soft)"/>
    <path d="M 240 523 H 750 L 776 491 H 934" fill="none" stroke="var(--green)" stroke-width="1"/>
  </svg>
  <div class="copy offer">
    <h2>Nuestra oferta <span class="accent">de valor</span></h2><span class="dash" style="margin-bottom:22px"></span>
    <p><span class="lead">Para nuestros fiados,</span>nos aseguramos de que el proceso de emisión de fianzas sea <span class="hl-green">claro, rápido y sencillo.</span> Dando una asesoría personalizada y seguimiento puntual a cada solicitud.</p>
    <p>Sabemos la importancia de tener una fianza en tiempo y sin errores, por lo que nos empeñamos en siempre ir un paso adelante, permitiendo que nuestros clientes se despreocupen del proceso de afianzamiento y logren todos sus objetivos.</p>
    <p class="lead-gap"><span class="lead">Para nuestros beneficiarios,</span>trabajamos solo con las mejores afianzadoras del país y garantizamos que todos nuestros clientes cuenten con una garantía confiable, que les permita concluir sus proyectos con la tranquilidad de que tienen un respaldo confiable. Nuestro compromiso es siempre mitigar los riesgos y nunca dejar desprotegidos a nuestros clientes</p>
  </div>
  <div class="footer-web"><span class="globe"></span>www.<span class="hl">talvoro</span>.com</div>
  <div class="wordmark footer-logo">Talvoro</div>
  <div class="page-no">3</div>
</section>

<!-- Services -->
<section class="slide slide--services">
  <svg class="art" viewBox="0 0 990 556">
    <defs><linearGradient id="servicesPhoto" x1="0" y1="0" x2="1" y2="1">
      <stop offset="0" stop-color="#dfe8ec"/><stop offset=".45" stop-color="#3f7fb6"/><stop offset=".75" stop-color="#1f4f86"/><stop offset="1" stop-color="#e07a3a"/></linearGradient></defs>
    <circle cx="773" cy="222" r="222" fill="url(#servicesPhoto)" role="img" aria-label="Casco de obra azul frente a edificios de la ciudad"/>
    <path d="M 660 -10 A 234 234 0 0 0 700 446" fill="none" stroke="var(--green)" stroke-width="1.5"/>
    <circle cx="608" cy="366" r="40" fill="var(--green-soft)"/>
    <circle cx="657" cy="412" r="24" fill="var(--green-soft)"/>
    <path d="M 240 523 H 750 L 776 491 H 934" fill="none" stroke="var(--green)" stroke-width="1"/>
  </svg>
  <div class="copy">
    <h2>Nuestros <span class="accent">Servicios</span></h2><span class="dash"></span>
    <ul class="services">
      <li>Asesoría personalizada para la obtención de Líneas de Afianzamiento</li>
      <li>Emisión y administración de fianzas.<small>(Fidelidad, Administrativas, Judiciales, Crédito y Fideicomisos)</small></li>
      <li>Diseño, implementación y gestión de esquemas de afianzamiento.</li>
      <li>Asesoría en riesgos para contratos de obra, suministro y proveeduría.</li>
      <li>Colocación de fianzas internacionales y reaseguro.</li>
      <li>Asesoría legal en proceso de reclamación de fianzas.</li>
      <li>Esquemas de afianzamiento masivos.</li>
    </ul>
  </div>
  <div class="footer-web"><span class="globe"></span>www.<span class="hl">talvoro</span>.com</div>
  <div class="wordmark footer-logo">Talvoro</div>
  <div class="page-no">4</div>
</section>

</body>
</html>
```